International Film making Business needs the 5 Logos provided made into a POSTER Format

Design Task:
CREATE A POSTER DESIGN USING THE 5 LOGOS PROVIDED. The BOLD BRIGHT HORIZON LOGO should stand out from the others by being in the middle with the other 4 logos connected to it somehow.

The 5 Businesses already has their 5 Logos, all similar in design to each other.

BOLD BRIGHT HORIZON is the Main Logo that encompasses the other 4 Logos. So it must stand out more and it is like the Overall Business entity that incorporates the other 4 Logos.

What is required is that by using the 5 Logo designs provided, create a cool graphic artwork that somehow incorporates ALL of the 5 Logos - But having the BOLD BRIGHT HORIZON Logo at the forefront/most important/standing out the most.
- BOLD BRIGHT HORIZON will probably be bigger than the others
- and could be changed into 3D.

I have attached all 5 logos and a hand drawn example of how the BOLD BRIGHT VISTAS could stand out from the rest.

THE DESIGNS OF THE LOGOS SHOULD NOT BE CHANGED (except the BOLDBRIGHTHORIZON which can be 3D)

Please do not be restricted with the sample idea. Creativity is encouraged

DIMENSION: 3000 mm x 6000 mm
high resolution graphic

Logo Text

bold bright , bold bright pictures, bold bright legends, bold bright groovy, BOLD BRIGHT VISTAS

Requirements
Must have
• USE THE 5 LOGOS PROVIDED ONLY - Only BOLD BRIGHT HORIZON can be changed into 3D only
Nice to have
• Eye catching design, showing the Bold Bright Horizon as the most powerful Logo that has the other 4 as subordinate companies
Should not have
• ANY CHANGE IN THE 5 LOGO DESIGNS (EXcept 3D for Bold Bright Horizons)

```html
<!DOCTYPE html>
<html lang="en">
<head>
<meta charset="utf-8">
<title>Bold Bright Vistas – Group Poster</title>
<link rel="stylesheet" href="https://fonts.googleapis.com/css2?family=Cinzel:wght@600;700&family=Raleway:wght@400&display=swap">
<style>
  :root {
    --frame-gold: #b07a2c;
    --white: #ffffff;
    --grey-text: #8a8a8a;
    --blue: #1f6fb8;
    --black: #1a1a1a;
    --purple: #5b2a86;
    --green: #1f7a3a;
    --title-gold: #b8892f;
  }
  * { margin: 0; padding: 0; box-sizing: border-box; }
  html, body { width: 1200px; height: 600px; overflow: hidden; background: var(--white); }
  .poster { position: relative; width: 1200px; height: 600px; overflow: hidden; }
  .poster-art { position: absolute; inset: 0; }
  .main-brand__line { font-family: "Cinzel", serif; font-weight: 600; font-size: 44px; fill: var(--title-gold); }
  .main-brand__url { font-family: "Raleway", sans-serif; font-weight: 400; font-size: 20px; fill: var(--grey-text); }
  .sub-brand {
    position: absolute; width: 220px; text-align: center;
    font-family: "Cinzel", serif; font-weight: 700;
    font-size: 25px; line-height: 30px; letter-spacing: 1px;
  }
  .sub-brand--core { left: 68px; top: 415px; color: var(--blue); }
  .sub-brand--pictures { left: 355px; top: 415px; color: var(--black); }
  .sub-brand--legends { left: 642px; top: 415px; color: var(--purple); }
  .sub-brand--groovy { left: 930px; top: 445px; color: var(--green); }
</style>
</head>
<body>
<main class="poster">
  <svg class="poster-art" viewBox="0 0 1200 600" width="1200" height="600" role="img" aria-label="Bold Bright Vistas group poster">
    <defs>
      <linearGradient id="goldSheen" x1="0" y1="0" x2="1" y2="1">
        <stop offset="0" stop-color="#b27d2b"/>
        <stop offset="0.25" stop-color="#f6e6a8"/>
        <stop offset="0.5" stop-color="#c99a45"/>
        <stop offset="0.75" stop-color="#f0dc9a"/>
        <stop offset="1" stop-color="#b27d2b"/>
      </linearGradient>
      <linearGradient id="bandBlue" x1="0" x2="1">
        <stop offset="0" stop-color="#263a8c"/><stop offset="0.45" stop-color="#1ba5de"/><stop offset="1" stop-color="#27398a"/>
      </linearGradient>
      <linearGradient id="bandGrey" x1="0" x2="1">
        <stop offset="0" stop-color="#050505"/><stop offset="0.5" stop-color="#8a8a8c"/><stop offset="1" stop-color="#050505"/>
      </linearGradient>
      <linearGradient id="bandSpectrum" x1="0" x2="1">
        <stop offset="0" stop-color="#5b2a8c"/><stop offset="0.2" stop-color="#26286e"/>
        <stop offset="0.45" stop-color="#1ba5de"/><stop offset="0.65" stop-color="#3cb54a"/>
        <stop offset="0.85" stop-color="#fff200"/><stop offset="1" stop-color="#f15a29"/>
      </linearGradient>
      <linearGradient id="bandGreen" x1="0" x2="1">
        <stop offset="0" stop-color="#0b6b3a"/><stop offset="0.55" stop-color="#8cc63f"/><stop offset="1" stop-color="#0b6b3a"/>
      </linearGradient>
    </defs>

    <rect class="header-field" x="0" y="0" width="1200" height="290" fill="url(#goldSheen)"/>

    <rect class="band band--core" x="0" y="290" width="318" height="310" fill="url(#bandBlue)"/>
    <rect class="band band--pictures" x="318" y="290" width="287" height="310" fill="url(#bandGrey)"/>
    <rect class="band band--legends" x="605" y="290" width="285" height="310" fill="url(#bandSpectrum)"/>
    <rect class="band band--groovy" x="890" y="290" width="310" height="310" fill="url(#bandGreen)"/>

    <polygon class="header-panel" points="475,12 741,12 1032,292 184,292"
             fill="var(--white)" stroke="var(--frame-gold)" stroke-width="12" stroke-linejoin="miter"/>

    <g class="diamond">
      <polygon points="178,289 332,443 178,597 24,443" fill="url(#goldSheen)"/>
      <polygon points="178,310 311,443 178,576 45,443" fill="var(--white)"/>
    </g>
    <g class="diamond">
      <polygon points="465,289 619,443 465,597 311,443" fill="url(#goldSheen)"/>
      <polygon points="465,310 598,443 465,576 332,443" fill="var(--white)"/>
    </g>
    <g class="diamond">
      <polygon points="752,289 906,443 752,597 598,443" fill="url(#goldSheen)"/>
      <polygon points="752,310 885,443 752,576 619,443" fill="var(--white)"/>
    </g>
    <g class="diamond">
      <polygon points="1040,289 1194,443 1040,597 886,443" fill="url(#goldSheen)"/>
      <polygon points="1040,310 1173,443 1040,576 907,443" fill="var(--white)"/>
    </g>

    <circle class="brand-dot" cx="445" cy="185" r="56" fill="var(--title-gold)"/>

    <g class="main-brand">
      <text class="main-brand__line" x="531" y="188" textLength="335" lengthAdjust="spacing">BOLD BRIGHT</text>
      <text class="main-brand__line" x="531" y="248" textLength="335" lengthAdjust="spacing">VISTAS</text>
      <text class="main-brand__url" x="531" y="276" textLength="335" lengthAdjust="spacing">boldbrightvistas.example</text>
    </g>
  </svg>

  <div class="sub-brand sub-brand--core">BOLD<br>BRIGHT</div>
  <div class="sub-brand sub-brand--pictures">BOLD BRIGHT<br>PICTURES</div>
  <div class="sub-brand sub-brand--legends">BOLD BRIGHT<br>LEGENDS</div>
  <div class="sub-brand sub-brand--groovy">BOLD BRIGHT<br>GROOVY</div>
</main>
</body>
</html>
```